Modern and professional facebook ad for disability service

Design a facebook ad for a disability service. Want something bright and fun and eyecatching. Would ideally like a carousel ad as this will give us more options to provide information.
CONTENT:
- Looking for a Plan Manager who will support your QWTR journey so that you can focus on living your best possible life and achieve your QWTR Goals?
- Then join the Wattlebrook Plan Management family today - quick and easy sign up.
- Friendly, Reliable, Responsive Service
- Dedicate Plan Managers so you always speak to the same person
- Fast Payment of Provider Invoices
- Supporting you to live Your Life, Your Way
- Call us today on 1300 482 316
- www.wattlebrookplanmanagement.com.au
Updates

Sick

Target Market(s)

Disability Sector

Font styles to use
Other font styles liked:
• Raleway

Requirements
Must have
• Bright colours and eye catching design

```html
<!DOCTYPE html>
<html lang="en">
<head>
<meta charset="utf-8">
<title>Wattlebrook Plan Management – Fast Payment of Provider Invoices</title>
<link rel="stylesheet" href="https://fonts.googleapis.com/css2?family=Raleway:wght@500;700&display=swap">
<style>
  :root {
    --plum: #6b2372;
    --violet-deep: #5b1f6c;
    --violet-bright: #8d1489;
    --leaf: #3fc552;
    --photo-green: #3a9e47;
    --photo-green-dark: #1f6b2b;
    --mist-blue: #c9daee;
    --white: #ffffff;
  }
  html, body {
    margin: 0;
    padding: 0;
    width: 1200px;
    height: 1200px;
    overflow: hidden;
    background: var(--white);
  }
  .ad-slide {
    position: relative;
    width: 1200px;
    height: 1200px;
    overflow: hidden;
    background: var(--white);
    font-family: "Raleway", Arial, sans-serif;
  }
  .shapes {
    position: absolute;
    inset: 0;
    width: 1200px;
    height: 1200px;
  }
  .feature-icon {
    position: absolute;
    left: 14px;
    top: 144px;
    width: 104px;
    height: 100px;
  }
  .feature-title {
    position: absolute;
    left: 140px;
    top: 124px;
    margin: 0;
    font-weight: 500;
    font-size: 82px;
    line-height: 105px;
    color: var(--plum);
    letter-spacing: -0.5px;
    white-space: nowrap;
  }
  .tagline {
    position: absolute;
    left: 1137px;
    top: 140px;
    margin: 0;
    font-weight: 700;
    font-size: 64px;
    line-height: 86px;
    color: var(--white);
    white-space: nowrap;
  }
</style>
</head>
<body>
<main class="ad-slide">
  <svg class="shapes" viewBox="0 0 1200 1200" xmlns="http://www.w3.org/2000/svg">
    <defs>
      <linearGradient id="violet-sweep" x1="0" y1="0" x2="1" y2="0">
        <stop offset="0" stop-color="var(--violet-deep)"/>
        <stop offset="1" stop-color="var(--violet-bright)"/>
      </linearGradient>
      <linearGradient id="photo-tone" x1="0" y1="0" x2="1" y2="1">
        <stop offset="0" stop-color="var(--photo-green)"/>
        <stop offset="1" stop-color="var(--photo-green-dark)"/>
      </linearGradient>
    </defs>

    <path class="violet-corner" d="M776,0 C800,140 950,420 1200,534 L1200,0 Z" fill="url(#violet-sweep)"/>

    <path class="accent-stroke" d="M172,460 C330,400 480,355 621,350 C730,346 830,380 914,428"
          fill="none" stroke="var(--leaf)" stroke-width="16" stroke-linecap="round"/>

    <path class="client-photo" role="img"
          aria-label="Photo of a smiling man in a wheelchair with a laptop on his lap, giving an OK hand sign, green duotone"
          d="M0,1200 L0,1000 C40,700 250,475 559,475 C760,475 900,600 950,850 C985,1030 1050,1130 1140,1200 Z"
          fill="url(#photo-tone)"/>

    <rect class="dot-cluster" role="img" aria-label="Decorative light blue dot pattern"
          x="1048" y="688" width="152" height="148" rx="20" fill="var(--mist-blue)" opacity="0.6"/>
  </svg>

  <svg class="feature-icon" viewBox="0 0 104 100" xmlns="http://www.w3.org/2000/svg" aria-hidden="true">
    <circle cx="48" cy="56" r="38" fill="none" stroke="var(--leaf)" stroke-width="12"/>
    <circle cx="48" cy="56" r="12" fill="none" stroke="var(--leaf)" stroke-width="8"/>
    <line x1="50" y1="54" x2="88" y2="14" stroke="var(--leaf)" stroke-width="6" stroke-linecap="round"/>
    <path d="M80,6 L86,0 L88,14 L102,16 L96,22 L82,20 Z" fill="var(--leaf)"/>
  </svg>

  <h1 class="feature-title">Fast Payment<br>of Provider Invoices</h1>

  <p class="tagline">Supporting you to<br>live Your Life,<br>Your Way</p>
</main>
</body>
</html>
```